Need a clean & modern homepage for an education site + opportunity for longer term work

Thanks for viewing our project. We are excited about this new website and we hope that we might build a relationship with designers as we work on this project. I provided quite a few details and requirements to help you more quickly create a design that meets our needs.
Who we are:
We are a website that discusses the importance of college accreditation and provides a directory of college programs.
What we need:
A homepage that meets the below requirements and is inspired by the examples provided
Definition of accredited:
ac·cred·it·ed [uh-kred-i-tid] adj.
1. officially recognized as meeting the essential requirements, as of academic excellence: accredited schools.
2. provided with official credentials, as by a government: an accredited diplomatic representative.
3. accepted as authoritative: an accredited theory.
Overall look and feel for the homepage:
- Clean, simple and modern
- Limited (or zero) pictures
- Utilize color blocks with text
- A trend seems to be longer vertical length homepages with lots of whitespace. I generally like this trend as long as the page is not way to tall.
Inspirations: Sites that have a similar look and feel to what I need.
http://lernvoxa.org/
http://www.campusmetrik.com/colleges/brantmoor-university/
http://quietfolding.org/
http://www.velostrahiring.com/
http://www.zunq.com/
http://sketches.bxv.com/
Items to be included on the homepage. Details below on each item.
- Top navigation
- Logo: Please leave a blank area for a logo. The logo has not been designed.
- Simple graphic/color block at the top that highlights a definition of “Accredited” – the definition should be formatted like it is being copy/pasted from a dictionary.
- Space for a video and small (50 word) written description of the video. You can use placeholder text.
- One section with 3 Paragraphs of content (each paragraph around 100 words) with a header at the top. You can use placeholder text but please create the formatting. At the end of the 3 paragraphs please have a “Read More” Note this shouldn't be 3 separate paragraphs with three read mores - it is 3 paragraphs with one read more at the end.
- An area with the header “Search Colleges by State” that has anchor text links to all 50 states.
Top navigation:
- Home
- States – with a subnav dropdown that includes all 50 US states.
- Programs – with a subnav dropdown that includes program titles (list below)
- Degrees - with a subnav dropdown that includes 5 degree levels (list below)
- Accreditation – no subnav
- Rankings – no subnav
- Resources – no subnav
Footer
- Link to about us, privacy, and a copyright www.url.com
Programs List for sub navigation
Accounting
Art
Bible
Business
Criminal Justice
Design
Education
Engineering
English
Law
LPN to RN
Management
Math
MBA
MPH
Medical Assisting
Military
Nursing
Occupational Therapy
Paralegal
Psychology
Pharmacy
RN to BSN
Radiology
Social Work
Sonography
Degrees list for sub navigation
Certificate
Associate
Bachelors
Masters
PhD
Thanks so much - looking forward to working with you!
Education

```html
<!DOCTYPE html>
<html lang="en">
<head>
<meta charset="utf-8">
<title>Accredited Colleges – Home</title>
<link rel="stylesheet" href="https://fonts.googleapis.com/css2?family=Jost:wght@400;500&family=Roboto+Condensed:wght@400&family=Arimo:wght@400&display=swap">
<style>
:root{
  --green:#137f66;
  --green-text:#1a8a6e;
  --ink:#222;
  --grey-text:#666a6e;
  --hero-bg:#e3e3e3;
  --feature-bg:#efeeec;
  --footer-bg:#5a5f63;
  --menu-bg:rgba(150,150,150,.88);
  --white:#fff;
}
*{margin:0;padding:0;box-sizing:border-box}
html,body{width:1200px;height:1164px;overflow:hidden}
body{position:relative;font-family:"Jost",sans-serif;color:var(--ink);background:var(--white)}
.abs{position:absolute}
.site-header{left:0;top:0;width:1200px;height:124px;background:linear-gradient(#dcdcdc,#fff 80%)}
.logo{left:151px;top:26px;font-size:63px;color:var(--grey-text);font-weight:400;letter-spacing:-1px}
.social{right:138px;top:2px;display:flex;gap:10px;font-size:12px;color:#6b6f73;font-weight:500}
.state-search{left:876px;top:83px;width:186px;height:30px;background:#9a9a9a;border:1px solid #c8c8c8;color:#fff;font-size:14px;line-height:28px;text-align:center}
.main-nav{left:0;top:124px;width:1200px;height:36px;background:var(--green)}
.main-nav a{position:absolute;top:7px;color:#fff;text-decoration:none;font-size:15.5px;font-weight:500}
.main-nav a.active{color:#7ee0c4}
.hero{left:0;top:160px;width:1200px;height:261px;background:var(--hero-bg);border-bottom:1px solid #f4f4f4}
.term{left:243px;top:216px;font-family:"Roboto Condensed",sans-serif;font-size:40px;color:var(--green);letter-spacing:1px}
.sense{left:246px;font-family:"Roboto Condensed",sans-serif;font-size:16.5px;color:#111}
.dropdown{left:316px;top:161px;width:579px;height:171px;background:var(--menu-bg)}
.dropdown span{position:absolute;font-size:13.5px;color:#fff;white-space:nowrap}
.dropdown .current{background:var(--green);left:0 !important;width:129px;height:25px;padding:3px 0 0 19px}
.feature{left:0;top:421px;width:1200px;height:343px;background:var(--feature-bg)}
.feature h2{left:200px;top:50px;width:360px;text-align:center;font-size:29px;font-weight:400;color:var(--green-text)}
.feature p{left:250px;top:104px;width:256px;text-align:center;font-size:13px;line-height:22.6px}
.video{left:671px;top:56px;width:317px;height:221px}
.columns{left:0;top:764px;width:1200px;height:293px}
.col{top:53px;width:260px;text-align:center}
.col h3{font-family:"Arimo",sans-serif;font-weight:400;font-size:23px;color:var(--green-text)}
.col p{margin:6px auto 0;width:206px;font-size:13.5px;line-height:20px}
.btn{display:inline-flex;align-items:center;gap:5px;margin-top:16px;height:30px;padding:0 12px;background:var(--green);color:#fff;font-family:"Arimo",sans-serif;font-size:12px;text-decoration:none}
.site-footer{left:0;top:1057px;width:1200px;height:107px;background:var(--footer-bg);color:#fff;font-size:14px}
.site-footer .links{left:153px;top:32px}
.site-footer .links span{font-size:11px;margin:0 6px}
.site-footer .copy{right:156px;top:33px;text-align:right;line-height:21px}
</style>
</head>
<body>
<header class="abs site-header">
  <div class="abs logo">Logo</div>
  <div class="abs social"><span>Facet</span><span>Chirpa</span><span>Linkwo</span><span>Plusly</span></div>
  <div class="abs state-search">Search Colleges by State</div>
</header>
<nav class="abs main-nav">
  <a style="left:154px">Home</a><a style="left:243px">States</a><a class="active" style="left:334px">Programs</a><a style="left:448px">Degrees</a><a style="left:555px">Accreditation</a><a style="left:696px">Rankings</a><a style="left:810px">Resources</a>
</nav>
<section class="abs hero" role="img" aria-label="Soft hexagon pattern background"></section>
<div class="abs term">ac·cred·it·ed</div>
<p class="abs sense" style="top:265px">- officially recognized as meeting the essential requirements, as of academic excellence: accredited schools.</p>
<p class="abs sense" style="top:297px">- provided with official credentials, as by a government: an accredited diplomatic representative.</p>
<p class="abs sense" style="top:323px">- accepted as authoritative: an accredited theory.</p>
<div class="abs dropdown">
  <span style="left:19px;top:4px">- Accounting</span><span style="left:19px;top:27px">- Art</span><span class="current" style="top:45px">- Bible</span><span style="left:19px;top:72px">- Business</span><span style="left:19px;top:95px">- Criminal Justice</span><span style="left:19px;top:117px">- Design</span><span style="left:19px;top:140px">- Education</span>
  <span style="left:155px;top:6px">- Engineering</span><span style="left:155px;top:29px">- English</span><span style="left:155px;top:51px">- Law</span><span style="left:155px;top:74px">- LPN to RN</span><span style="left:155px;top:97px">- Management</span><span style="left:155px;top:119px">- Math</span><span style="left:155px;top:142px">- MBA</span>
  <span style="left:276px;top:6px">- MPH</span><span style="left:276px;top:29px">- Medical Assisting</span><span style="left:276px;top:51px">- Military</span><span style="left:276px;top:74px">- Nursing</span><span style="left:276px;top:97px">- Occupational Therapy</span><span style="left:276px;top:119px">- Paralegal</span><span style="left:276px;top:142px">- Psychology</span>
  <span style="left:451px;top:7px">- Pharmacy</span><span style="left:451px;top:30px">- RN to BSN</span><span style="left:451px;top:52px">- Radiology</span><span style="left:451px;top:75px">- Social Work</span><span style="left:451px;top:98px">- Sonography</span>
</div>
<section class="abs feature">
  <h2 class="abs">Lorem Ipsum proin gra</h2>
  <p class="abs">Lorem Ipsum proin gravida nibh vel velit auctor aliquet. Aenean sollicitudin, lorem bibendum auctor, nisi elit consequat ipsum, nec sagittis sem nibh id elit. Duis sed odio sit amet nibh vulputate a sit</p>
  <svg class="abs video" viewBox="0 0 317 221" role="img" aria-label="Video still of a blurred campus building with a play button">
    <defs><linearGradient id="still" x1="0" y1="0" x2="1" y2="1"><stop offset="0" stop-color="#8f8a80"/><stop offset=".5" stop-color="#c9c6bd"/><stop offset="1" stop-color="#6f7a68"/></linearGradient></defs>
    <rect width="317" height="221" fill="url(#still)"/>
    <circle cx="158" cy="115" r="52" fill="none" stroke="#137f66" stroke-width="12"/>
    <path d="M142 91v48l36-24z" fill="#137f66"/>
  </svg>
</section>
<section class="abs columns">
  <div class="abs col" style="left:159px"><h3>Lorem Ipsum proin gra</h3><p>Lorem Ipsum proin gravida nibh vel velit auctor aliquet. sollicitudin, lorem bibendum nisi elit consequat ipsum, necid elit. Duis sed odio</p><a class="btn">Read More <svg width="9" height="12" viewBox="0 0 9 12"><path d="M2 1l5 5-5 5" fill="none" stroke="#fff" stroke-width="2.4"/></svg></a></div>
  <div class="abs col" style="left:467px"><h3>Lorem Ipsum proin gra</h3><p>Lorem Ipsum proin gravida nibh vel velit auctor aliquet. sollicitudin, lorem bibendum nisi elit consequat ipsum, necid elit. Duis sed odio</p><a class="btn">Read More <svg width="9" height="12" viewBox="0 0 9 12"><path d="M2 1l5 5-5 5" fill="none" stroke="#fff" stroke-width="2.4"/></svg></a></div>
  <div class="abs col" style="left:775px"><h3>Lorem Ipsum proin gra</h3><p>Lorem Ipsum proin gravida nibh vel velit auctor aliquet. sollicitudin, lorem bibendum nisi elit consequat ipsum, necid elit. Duis sed odio</p><a class="btn">Read More <svg width="9" height="12" viewBox="0 0 9 12"><path d="M2 1l5 5-5 5" fill="none" stroke="#fff" stroke-width="2.4"/></svg></a></div>
</section>
<footer class="abs site-footer">
  <div class="abs links">About us<span>|</span>Privacy Policy</div>
  <div class="abs copy">Copyright © 2013 companyname.com<br>All Rights Reserved.</div>
</footer>
</body>
</html>
```